Thoroughbred Racing Partnership needs web design

Glimmer of Laurel Partners is a management group who buys horses and races them on both the West and East coasts. The premise of the business is for an investment as little as $500, anyone can be a partner and own a percentage of a horse(s). This is a low cost way of getting involved in the exciting sport of Thoroughbred Racing, without shouldering the heavy financial responsibility. Our target market is mostly males 40+ but we want to include all target markets. We are looking for something very clean and professional, we want to give an image of success. Nothing overly "artsy." I have included the logo in which you can incorporate in the site. Also, the logo colors will be the colors of our "silks." The silks are what the jockey wears and will be an important marketing tool for GOL. We would like a very prominent picture of a racehorse somewhere on the homepage, we want to make it clear that is a website for Horseracing partnerships.

On the top of the site, it should say "Glimmer of Laurel" (on the top)
and below that "Thoroughbred Racing Partnerships." (below that)

The main sections, which should be across the top are:

Home
About Us
Ownership
Stable Roster
News
Contact us

Some of these will have drop down menus.

An example of a competitor website that we like is: www.harrowgatefarm.example
An example of a competitor website that we don't like is: www.paddockvue.example
Updates

Project Deadline Extended
Reason: We have a Board of Directors meeting on the 22nd and we will be making a decision on that day. I'm giving an extension so that all designers are able to submit their designs by the 22nd. Thank you!

Target Market(s)

40+ males

Industry/Entity Type

Business

Requirements
Must have
• our logo must be on the site. We would like at least one bold image of a thoroughbred horse in action. The picture is going to tell the story so it needs to be very eye-catching.

Our slogan should also be included on the website, "Experience the thrill of owning a Racehorse."
Should not have
• cartoons, artsy pictures, pictures of Steeplechase horses or "jumpers." This partnership is for racehorses only, there is not jumping involved with the horses.

```html
<!DOCTYPE html>
<html lang="en">
<head>
<meta charset="utf-8">
<title>Glimmer of Laurel Partners – Thoroughbred Racing Partnerships</title>
<link href="https://fonts.googleapis.com/css2?family=Oswald:wght@400;500&family=Open+Sans:ital,wght@0,400;0,600;0,700;1,400&display=swap" rel="stylesheet">
<style>
:root{
  --header-blue:#0f4f87;
  --band-blue:#12508a;
  --panel-navy:#0b1c4d;
  --footer-blue:#0c3864;
  --footer-line:#2a5a88;
  --page-gray:#e5e5e5;
  --panel-top:#f7f7f7;
  --panel-bottom:#dcdcdc;
  --ink:#2b2b2b;
  --navy-text:#0d2c5c;
  --link-blue:#1a5c98;
  --sky:#4aa9ea;
  --white:#ffffff;
  --pill:#dfeaf3;
  --button:#0f4f87;
}
*{box-sizing:border-box;margin:0;padding:0}
html,body{width:1059px;height:1200px;overflow:hidden;background:var(--page-gray)}
body{position:relative;font-family:"Open Sans",Arial,sans-serif;color:var(--ink)}
.abs{position:absolute}

/* header */
.site-header{left:0;top:0;width:1059px;height:103px;background:var(--header-blue)}
.brand{left:126px;top:6px;width:170px;color:#dce8f2;font-weight:700;line-height:1}
.brand-initials{font-size:52px;letter-spacing:6px;display:block}
.brand-domain{font-size:19px;display:block;margin-top:2px;letter-spacing:.5px}
.tagline{left:687px;top:9px;color:#dfe9f3;font-style:italic;font-size:14.5px;line-height:22px}
.main-nav{left:398px;top:69px;display:flex;align-items:center}
.main-nav a{color:var(--white);text-decoration:none;font-size:11.5px;font-weight:700;letter-spacing:.3px;padding:5px 8px;position:relative}
.main-nav a + a::before{content:"";position:absolute;left:-6px;top:5px;height:14px;border-left:1px solid #3a74a8}
.main-nav a{margin-right:12px}
.main-nav a.is-active{background:linear-gradient(#f2f7fb,#c9dcec);color:var(--navy-text);border-radius:4px}

/* hero */
.hero{left:0;top:103px;width:1059px;height:457px}
.hero-photo{position:absolute;inset:0;background:linear-gradient(180deg,#e9f0e2 0%,#4f7b3a 30%,#6c9247 60%,#7aa24f 100%)}
.hero-title{left:532px;top:113px;font-family:"Oswald",sans-serif;font-weight:400;font-size:32px;line-height:38px;color:var(--navy-text);letter-spacing:-.2px}
.slider-dots{left:815px;top:532px;display:flex;gap:4px}
.slider-dots span{width:31px;height:7px;background:var(--header-blue)}
.slider-dots span.is-current{background:var(--white)}

/* intro band */
.intro{left:0;top:560px;width:1059px;height:194px;background:var(--band-blue)}
.intro-title{left:126px;top:12px;width:526px;padding-bottom:6px;border-bottom:1px solid #6f9bc3;font-family:"Oswald",sans-serif;font-weight:400;font-size:22px;color:var(--white)}
.intro-text{left:126px;top:62px;width:535px;font-size:11.6px;line-height:18.5px;font-weight:700;color:var(--white)}
.btn-light{left:566px;top:151px;width:79px;height:20px;border-radius:4px;background:linear-gradient(#ffffff,#dbe6ef);color:var(--link-blue);font:700 10px/20px Arial,sans-serif;text-align:center}
.video{left:683px;top:11px;width:250px;height:171px;border:1px solid #ffffff;background:#111}
.video-still{position:absolute;left:0;top:0;width:248px;height:145px;background:linear-gradient(180deg,#1a1a1a 0%,#3a3a3a 55%,#6b6f78 100%)}
.video-play{position:absolute;left:102px;top:56px}
.video-bar{position:absolute;left:0;bottom:0;width:248px;height:24px;background:linear-gradient(#3a3a3a,#1c1c1c);color:#ddd;font-size:8px}
.video-time{position:absolute;left:82px;top:7px}

/* panels */
.panel{top:777px;width:265px;height:246px;border-radius:6px;background:linear-gradient(var(--panel-top),var(--panel-bottom));box-shadow:0 3px 4px rgba(0,0,0,.18)}
.panel-head{height:33px;background:var(--panel-navy);border-radius:6px 6px 0 0;position:relative}
.panel-icon{position:absolute;left:7px;top:-2px;width:36px;height:36px;border-radius:50%;background:var(--white);border:2px solid var(--panel-navy)}
.panel-icon svg{position:absolute;left:7px;top:7px}
.panel-title{position:absolute;left:63px;top:1px;font-family:"Oswald",sans-serif;font-size:22px;color:var(--white);line-height:32px}
.panel-body{padding:9px 9px 0 9px;font-size:10.3px;line-height:16.3px;color:#333}
.ticks{list-style:none;margin-top:8px}
.ticks li{position:relative;padding-left:24px;color:var(--link-blue);font-weight:600;font-size:10.3px;line-height:18.5px}
.ticks svg{position:absolute;left:2px;top:4px}
.btn-dark{position:absolute;width:79px;height:19px;border-radius:3px;background:var(--button);color:var(--white);font:700 10px/19px Arial,sans-serif;text-align:center}
.testimonial-photo{position:absolute;left:12px;top:55px;width:66px;height:70px;background:linear-gradient(#c8d3dc,#8d9aa6);border:1px solid #bbb}
.quote{position:absolute;left:94px;top:50px;width:160px;font-size:10.2px;line-height:17.3px;color:#444}
.quote-mark{color:#999;font-family:Georgia,serif;font-size:16px;margin-right:3px}
.quote-name{position:absolute;left:94px;top:152px;font-weight:700;font-size:12px;color:var(--link-blue)}
.quote-role{position:absolute;left:94px;top:174px;font-weight:700;font-size:11.5px;color:#333}
.field{position:absolute;left:9px;width:240px;height:23px;border:1px solid #cfcfcf;border-radius:2px;background:#fafafa;font-size:10px;color:#555;padding:4px 8px}

/* footer */
.site-footer{left:0;top:1046px;width:1059px;height:154px;background:var(--footer-blue)}
.footer-col{top:20px}
.footer-title{font-size:13.5px;font-weight:600;color:var(--sky);padding-bottom:2px;border-bottom:1px dashed var(--footer-line)}
.footer-divider{top:8px;width:1px;height:138px;background:#174a7c}
.footer-links{list-style:none;margin:10px 0 0 8px;font-size:10.3px;line-height:15px;color:var(--white)}
.footer-links li:first-child{color:var(--sky)}
.footer-text{font-size:10.3px;line-height:16px;color:var(--white);margin:8px 0 0 3px}
.email-input{margin:12px 0 0 2px;width:146px;height:22px;border:1px solid #2c76b6;background:#0d4e87;color:#8cb7dd;font-style:italic;font-size:9px;padding:5px 4px}
.signup-btn{margin:8px 0 0 75px;width:72px;height:21px;border-radius:3px;background:linear-gradient(#ffffff,#d5dee6);color:var(--navy-text);font-weight:700;font-size:11px;text-align:center;line-height:21px}
.contact-line{display:flex;align-items:center;gap:8px;font-weight:700;font-size:10.5px;color:var(--white);margin:4px 0 0 3px;height:20px}
.footer-brand{left:791px;top:18px;width:120px;color:#dce8f2;font-weight:700;line-height:1;text-align:center}
.footer-brand .brand-initials{font-size:36px;letter-spacing:4px}
.footer-brand .brand-domain{font-size:14px}
.social{left:788px;top:99px;display:flex;gap:8px}
.social span{width:25px;height:25px;border-radius:50%;background:#2f86c9}
.copyright{left:785px;top:122px;font-family:Arial,sans-serif;font-size:8.5px;color:var(--white)}
</style>
</head>
<body>

<header class="site-header abs">
  <div class="brand abs"><span class="brand-initials">GOL</span><span class="brand-domain">PARTNERS.COM</span></div>
  <p class="tagline abs">Glimmer of Laurel<br>Thoroughbred Racing Partnerships.</p>
  <nav class="main-nav abs">
    <a class="is-active">HOME</a><a>ABOUT US</a><a>OWNERSHIP</a><a>STABLE ROSTER</a><a>NEWS</a><a>CONTACT US</a>
  </nav>
</header>

<section class="hero abs">
  <div class="hero-photo" role="img" aria-label="Thoroughbred racehorses with jockeys galloping down the turf stretch beside a white rail"></div>
  <h1 class="hero-title abs" style="top:10px">Feel the exhilaration of<br>the stretch run.</h1>
  <div class="slider-dots abs" style="top:429px"><span class="is-current"></span><span></span><span></span></div>
</section>

<section class="intro abs">
  <h2 class="intro-title abs">Glimmer of Laurel Thoroughbred Partnerships</h2>
  <p class="intro-text abs">Glimmer of Laurel Partners is a management group who buys horses and races them on both the West and East coasts. The premise of the business is for an investment as little as $500, anyone can be a partner and own a percentage of a horse(s). This is a low cost way of getting involved in the exciting sport of Thoroughbred Racing, without shouldering the heavy financial responsibility.</p>
  <div class="btn-light abs">Read more »</div>
  <div class="video abs">
    <div class="video-still" role="img" aria-label="Video still of three partners holding a racing award plaque"></div>
    <svg class="video-play" width="46" height="40" viewBox="0 0 46 40"><rect width="46" height="40" rx="6" fill="#c8242a"/><path d="M17 10 L33 20 L17 30 Z" fill="#fff"/></svg>
    <div class="video-bar">
      <svg style="position:absolute;left:20px;top:7px" width="40" height="11" viewBox="0 0 40 11"><rect x="0" y="0" width="3" height="11" fill="#ccc"/><rect x="6" y="0" width="3" height="11" fill="#ccc"/><path d="M28 4h3l4-3v9l-4-3h-3z" fill="#ccc"/></svg>
      <span class="video-time">0:00 / 0:00</span>
      <svg style="position:absolute;right:12px;top:6px" width="44" height="12" viewBox="0 0 44 12"><path d="M2 9h8V3M8 5l2-2 2 2" stroke="#ccc" fill="none"/><path d="M30 1h4M30 1v4M43 11h-4M43 11v-4M30 11h4M30 11v-4M43 1h-4M43 1v4" stroke="#ccc" fill="none"/></svg>
    </div>
  </div>
</section>

<section class="panel abs" style="left:124px">
  <div class="panel-head">
    <div class="panel-icon"><svg width="18" height="18" viewBox="0 0 18 18"><circle cx="9" cy="9" r="8" fill="none" stroke="#0f4f87" stroke-width="2"/></svg></div>
    <h3 class="panel-title">Ownership Pride</h3>
  </div>
  <div class="panel-body">
    <p>Lorem ipsum dolor sit amet, consectet adipiscing elit, sed diam nonummy nibh euismod tincidunt ut laoreet dolore magna aliquam erat volutpat.Ut wisi enim ad minim veniam, quis nostru exe ullamcorper suscipit lobortis nisl ut aliquip commod consequat.</p>
    <ul class="ticks">
      <li><svg width="14" height="12" viewBox="0 0 14 12"><path d="M1 7l4 4L13 1" stroke="#1a6fb4" stroke-width="1.6" fill="none"/></svg>Lorem ipsum dolor sit amet</li>
      <li><svg width="14" height="12" viewBox="0 0 14 12"><path d="M1 7l4 4L13 1" stroke="#1a6fb4" stroke-width="1.6" fill="none"/></svg>Sed diam nonummy nibh euismod</li>
      <li><svg width="14" height="12" viewBox="0 0 14 12"><path d="M1 7l4 4L13 1" stroke="#1a6fb4" stroke-width="1.6" fill="none"/></svg>Ut wisi enim ad minim</li>
      <li><svg width="14" height="12" viewBox="0 0 14 12"><path d="M1 7l4 4L13 1" stroke="#1a6fb4" stroke-width="1.6" fill="none"/></svg>Consectet adipiscing elit</li>
    </ul>
  </div>
  <div class="btn-dark" style="left:169px;top:217px">Read more »</div>
</section>

<section class="panel abs" style="left:397px">
  <div class="panel-head">
    <div class="panel-icon"><svg width="20" height="18" viewBox="0 0 20 18"><path d="M1 2h11v7H6l-3 3V9H1z" fill="#0f4f87"/><path d="M8 10h5l0-4h6v7h-2v3l-3-3H8z" fill="#0f4f87"/></svg></div>
    <h3 class="panel-title">Client Testimonials</h3>
  </div>
  <div class="testimonial-photo" role="img" aria-label="Portrait of a client in business attire"></div>
  <p class="quote"><span class="quote-mark">“</span>Ut wisi enim ad mini veniam, quis nostrud exerci tationullamo corper suscipit lobortis nislutalil uip  ullamcorper suscipit lobortis aliquip commod consequat.</p>
  <p class="quote-name">Mr. Lorem ipsum sit amet</p>
  <p class="quote-role">Chief Executive</p>
  <div class="btn-dark" style="left:171px;top:218px">Read more »</div>
</section>

<section class="panel abs" style="left:670px">
  <div class="panel-head">
    <div class="panel-icon"><svg width="18" height="20" viewBox="0 0 18 20"><path d="M2 1h10l4 4v14H2z" fill="none" stroke="#0f4f87" stroke-width="1.8"/><path d="M6 14l6-7 2 2-6 7H6z" fill="#0f4f87"/></svg></div>
    <h3 class="panel-title">Quick Contact</h3>
  </div>
  <div class="field" style="top:50px">Your Name</div>
  <div class="field" style="top:78px">Email</div>
  <div class="field" style="top:107px">Phone</div>
  <div class="field" style="top:136px;height:63px">Message</div>
  <div class="btn-dark" style="left:169px;top:216px">Submit</div>
</section>

<footer class="site-footer abs">
  <div class="footer-col abs" style="left:126px;width:98px">
    <h4 class="footer-title">Quick Links</h4>
    <ul class="footer-links"><li>Home</li><li>About Us</li><li>Ownership</li><li>Stable Roster</li><li>News</li><li>Contact us</li></ul>
  </div>
  <div class="footer-divider abs" style="left:264px"></div>
  <div class="footer-col abs" style="left:301px;width:166px">
    <h4 class="footer-title">Newsletter Signup</h4>
    <p class="footer-text" style="line-height:12px">Signup with us and get news and update in your inbox</p>
    <div class="email-input">Email here</div>
    <div class="signup-btn">Signup</div>
  </div>
  <div class="footer-divider abs" style="left:505px"></div>
  <div class="footer-col abs" style="left:543px;width:166px">
    <h4 class="footer-title">Company Headquarter</h4>
    <p class="footer-text">Lorem ipsum dolor sit amet<br>consectetuer adipsi<br>Po Box-0050</p>
    <div class="contact-line"><svg width="12" height="12" viewBox="0 0 12 12"><path d="M2 1l2 0 1 3-1.5 1a7 7 0 0 0 3.5 3.5L8 7l3 1v2c0 1-1 1-1 1A9 9 0 0 1 1 2c0 0 0-1 1-1z" fill="#cfe0ef"/></svg>001 555-0148</div>
    <div class="contact-line"><svg width="14" height="10" viewBox="0 0 14 10"><rect x=".5" y=".5" width="13" height="9" fill="none" stroke="#cfe0ef"/><path d="M.5 .5L7 6l6.5-5.5" fill="none" stroke="#cfe0ef"/></svg>info@golpartners.example</div>
  </div>
  <div class="footer-divider abs" style="left:746px"></div>
  <div class="footer-brand abs"><span class="brand-initials">GOL</span><span class="brand-domain">PARTNERS.COM</span></div>
  <div class="social abs" aria-label="Social profiles"><span></span><span></span><span></span><span></span></div>
  <p class="copyright abs">© 2013 Glimmer of Laurel Partners</p>
</footer>

</body>
</html>
```